Navoro & Omvar Automotive Repair Shop. Need a new website design.

We specialize in Navoro & Omvar auto repair, but also work on other Asian import vehicles. We have been in business for 7 years and pride ourselves on high quality auto repair that is fixed right the first time. Would like the automotive repair website to incorporate the colors black, red and white if possible and have our logo and some Navoro and Omvar vehicles included in the website.

Target Market(s)

Navoro & Omvar vehicle owners

Industry/Entity Type

Automotive Repair

Coding

Coded - Design and coding required

Number of Pages Required

5+ page

Colors
EB3D1F
EC4F4E
F09395
F8D3D4
FCEDEE

Requirements
Must have
• Home, Services, Contact Us, Schedule appointment, and a gallery tab that I can add shop pictures to when completed.
Nice to have
• Would like to see example pictures of job next to each service listed.
Should not have
• Service not related to auto repair. Ex. auto detailing, towing, car wash

```html
<!DOCTYPE html>
<html lang="en">
<head>
<meta charset="utf-8">
<title>Rivo Automotive – Website Design</title>
<link rel="stylesheet" href="https://fonts.googleapis.com/css2?family=Michroma&family=Roboto:wght@400;700&display=swap">
<style>
:root{
  --board:#8e8e8e;
  --ink:#0a0a0a;
  --panel:#151515;
  --panel-2:#1f1f1f;
  --line:#2c2c2c;
  --red:#eb3d1f;
  --red-2:#ec4f4e;
  --rose:#f09395;
  --blush:#f8d3d4;
  --white:#ffffff;
  --muted:#b9b9b9;
  --head:"Michroma",sans-serif;
  --body:"Roboto",sans-serif;
}
*{box-sizing:border-box;margin:0;padding:0}
html,body{width:727px;height:1200px;overflow:hidden}
body{background:var(--board);font-family:var(--body);color:var(--white);position:relative}
.page{position:absolute;top:12px;width:338px;height:1176px;background:var(--ink);overflow:hidden;box-shadow:0 2px 8px rgba(0,0,0,.35)}
.page--a{left:18px}
.page--b{left:371px}
.section{position:absolute;left:0;width:100%}

/* nav */
.nav{top:0;height:22px;background:#000;display:flex;align-items:center;justify-content:center;gap:12px;font-size:5px;letter-spacing:.5px;z-index:3}
.nav__brand{display:flex;align-items:center;gap:3px;font-weight:700;font-size:7px;color:var(--white)}
.dot{width:7px;height:7px;border-radius:50%;background:var(--red)}
.nav__cta{border:1px solid var(--red);padding:2px 5px;border-radius:2px}

/* hero */
.hero{top:22px;height:165px}
.hero__photo{position:absolute;inset:0;background:linear-gradient(100deg,#0c0c0c 0%,#2a2a2a 45%,#5a5a5a 70%,#2b2b2b 100%)}
.hero__copy{position:absolute;left:22px;top:34px;width:170px}
.hero__title{font-family:var(--head);font-size:10.5px;line-height:1.35;text-transform:uppercase}
.hero__title em{font-style:normal;color:var(--red)}
.hero__sub{font-size:5.5px;color:var(--muted);margin:6px 0 9px}
.btn{display:inline-block;background:var(--red);color:var(--white);font-size:5px;font-weight:700;letter-spacing:.5px;padding:4px 9px;border-radius:2px}
.btn--ghost{background:none;border:1px solid var(--white)}
.hero__edge{position:absolute;left:0;bottom:0;width:100%;height:30px}

/* about */
.about{top:187px;height:160px;display:flex;align-items:center;padding:0 18px;gap:16px}
.about__mark{width:118px;height:96px;display:flex;align-items:center;justify-content:center;gap:6px;font-weight:700;font-size:22px}
.about__mark .dot{width:18px;height:18px}
.about__text{flex:1}
.h2{font-family:var(--head);font-size:10px;letter-spacing:.5px;margin-bottom:6px}
.about__text p{font-size:5px;line-height:1.55;color:var(--muted);margin-bottom:8px}

/* services */
.services{top:347px;height:205px;background:var(--panel);padding:16px 14px 0}
.center{text-align:center}
.services__grid{display:grid;grid-template-columns:repeat(3,1fr);gap:0 8px;margin-top:10px}
.svc{display:flex;align-items:center;gap:4px;height:20px;border-bottom:1px solid var(--line);font-size:5px;text-transform:uppercase}
.svc__icon{width:7px;height:7px;border:1px solid var(--red);border-radius:50%;flex:none}
.svc--active{background:var(--red);padding-left:3px}
.svc--active .svc__icon{border-color:var(--white)}

/* gallery */
.gallery{top:552px;height:190px;background:linear-gradient(180deg,#3a3a3a,#1b1b1b)}
.gallery__edge{position:absolute;top:0;left:0;width:100%;height:24px}
.gallery .h2{position:relative;margin-top:32px}
.gallery__grid{display:grid;grid-template-columns:repeat(4,1fr);gap:4px;padding:8px 18px 0}
.shot{height:56px;background:linear-gradient(135deg,#6c6c6c,#2d2d2d)}
.shot:nth-child(3n+2){background:linear-gradient(135deg,#8a8f96,#3e4247)}
.shot:nth-child(4n){background:linear-gradient(135deg,#5b4a3f,#262626)}

/* brands */
.brands{top:742px;height:155px;background:#000;padding:22px 30px 0;text-align:center}
.brands__text{font-family:var(--head);font-size:5.5px;line-height:1.6;letter-spacing:.3px}
.brands__row{display:grid;grid-template-columns:repeat(4,1fr);gap:10px 18px;margin:12px 20px 12px}
.badge{height:20px;border-radius:50%;background:#6f6f6f;width:34px;margin:0 auto}
.badge--sq{border-radius:3px;background:#9a9a9a}

/* contact */
.contact{top:897px;height:205px;background:radial-gradient(circle at 25% 40%,#3a1410 0%,#141414 55%);display:flex;padding:30px 18px 0;gap:18px}
.contact__info{flex:1}
.contact__title{font-family:var(--head);font-size:13px}
.contact__title em{font-style:normal;color:var(--red)}
.contact__info p{font-size:5px;line-height:1.6;color:var(--muted);margin:6px 0}
.contact__line{display:flex;align-items:center;gap:4px;font-size:5px;margin-bottom:4px}
.contact__form{flex:1}
.form__label{font-size:5.5px;font-weight:700;letter-spacing:.4px;margin-bottom:6px}
.field{height:13px;border:1px solid #3a3a3a;background:#0e0e0e;font-size:4.5px;color:#777;padding:3px 4px;margin-bottom:5px}
.field--area{height:34px}

/* footer */
.footer{top:1102px;height:74px;background:#000;text-align:center}
.footer__edge{position:absolute;top:0;left:0;width:100%;height:14px}
.footer__brand{display:inline-flex;align-items:center;gap:3px;font-weight:700;font-size:8px;margin-top:14px}
.footer__nav{display:flex;justify-content:center;gap:12px;font-size:4.5px;margin:6px 0}
.footer__badges{display:flex;justify-content:center;gap:10px}
.footer__badges span{width:26px;height:9px;background:#555;border-radius:2px}
</style>
</head>
<body>

<main class="page page--a">
  <nav class="section nav">
    <span>HOME</span><span>ABOUT</span>
    <span class="nav__brand"><span class="dot"></span>RIVO</span>
    <span>SERVICES</span><span>GALLERY</span><span class="nav__cta">BOOK NOW</span>
  </nav>
  <header class="section hero">
    <div class="hero__photo" role="img" aria-label="Engine bay of a car under repair"></div>
    <div class="hero__copy">
      <h1 class="hero__title">Specializing in Navoro and Omvar <em>auto repair</em></h1>
      <p class="hero__sub">Fixed right the first time, every visit.</p>
      <span class="btn">SCHEDULE APPOINTMENT</span>
    </div>
    <svg class="hero__edge" viewBox="0 0 338 30" preserveAspectRatio="none"><polygon points="0,8 169,26 338,8 338,30 0,30" fill="#0a0a0a"/><polyline points="0,8 169,26 338,8" fill="none" stroke="#eb3d1f" stroke-width="2"/></svg>
  </header>
  <section class="section about">
    <div class="about__mark"><span class="dot"></span>RIVO</div>
    <div class="about__text">
      <h2 class="h2">ABOUT RIVO</h2>
      <p>For seven years our certified technicians have cared for Navoro and Omvar owners, plus other Asian imports. We use quality parts, honest pricing and careful work so every repair is done right the first time.</p>
      <span class="btn btn--ghost">LEARN MORE</span>
    </div>
  </section>
  <section class="section services">
    <h2 class="h2 center">SERVICES PROVIDE</h2>
    <div class="services__grid">
      <div>
        <div class="svc svc--active"><i class="svc__icon"></i>Oil Change</div>
        <div class="svc"><i class="svc__icon"></i>Brake Repair</div>
        <div class="svc"><i class="svc__icon"></i>Engine Diagnostics</div>
        <div class="svc"><i class="svc__icon"></i>Tune Up</div>
        <div class="svc"><i class="svc__icon"></i>Timing Belt</div>
        <div class="svc"><i class="svc__icon"></i>Battery Service</div>
      </div>
      <div>
        <div class="svc"><i class="svc__icon"></i>Transmission Service</div>
        <div class="svc"><i class="svc__icon"></i>Suspension Repair</div>
        <div class="svc"><i class="svc__icon"></i>Steering Repair</div>
        <div class="svc"><i class="svc__icon"></i>Cooling System</div>
        <div class="svc"><i class="svc__icon"></i>Exhaust Repair</div>
        <div class="svc"><i class="svc__icon"></i>Wheel Alignment</div>
      </div>
      <div>
        <div class="svc"><i class="svc__icon"></i>AC Repair</div>
        <div class="svc"><i class="svc__icon"></i>Electrical Repair</div>
        <div class="svc"><i class="svc__icon"></i>Check Engine Light</div>
        <div class="svc"><i class="svc__icon"></i>Fuel System</div>
        <div class="svc"><i class="svc__icon"></i>Hybrid Service</div>
        <div class="svc"><i class="svc__icon"></i>Inspections</div>
      </div>
    </div>
  </section>
  <section class="section gallery">
    <svg class="gallery__edge" viewBox="0 0 338 24" preserveAspectRatio="none"><polygon points="0,0 338,0 338,4 169,22 0,4" fill="#151515"/></svg>
    <h2 class="h2 center">OUR GALLERY</h2>
    <div class="gallery__grid">
      <div class="shot" role="img" aria-label="Shop photo of engine work"></div>
      <div class="shot" role="img" aria-label="Shop photo of a sedan on the lift"></div>
      <div class="shot" role="img" aria-label="Shop photo of engine parts"></div>
      <div class="shot" role="img" aria-label="Shop photo of a technician's bench"></div>
      <div class="shot" role="img" aria-label="Shop photo of an SUV in the bay"></div>
      <div class="shot" role="img" aria-label="Shop photo of a car in the lot"></div>
      <div class="shot" role="img" aria-label="Shop photo of cars outside the shop"></div>
      <div class="shot" role="img" aria-label="Shop photo of a repaired vehicle"></div>
    </div>
  </section>
  <section class="section brands">
    <p class="brands__text">RIVO AUTOMOTIVE SPECIALIZES IN NAVORO &amp; OMVAR<br>AUTO REPAIR BUT ALSO SERVICE AND REPAIR<br>OTHER ASIAN IMPORT VEHICLES</p>
    <div class="brands__row">
      <span class="badge"></span><span class="badge badge--sq"></span><span class="badge"></span><span class="badge badge--sq"></span>
      <span class="badge badge--sq"></span><span class="badge"></span><span class="badge badge--sq"></span><span class="badge"></span>
    </div>
    <span class="btn">SCHEDULE APPOINTMENT</span>
  </section>
  <section class="section contact">
    <div class="contact__info">
      <h2 class="contact__title">CONTACT <em>US</em></h2>
      <p>Questions about your vehicle? Call or send a message and we will reply soon.</p>
      <div class="contact__line"><span class="dot"></span>(555) 018-2247</div>
      <div class="contact__line"><span class="dot"></span>hello@rivoauto.example</div>
      <div class="contact__line"><span class="dot"></span>120 Harbor Lane, Springvale</div>
    </div>
    <form class="contact__form">
      <div class="form__label">LEAVE US A MESSAGE</div>
      <div class="field">Name</div>
      <div class="field">Email</div>
      <div class="field">Phone</div>
      <div class="field field--area">Message</div>
      <span class="btn">SEND</span>
    </form>
  </section>
  <footer class="section footer">
    <svg class="footer__edge" viewBox="0 0 338 14" preserveAspectRatio="none"><polyline points="0,12 169,2 338,12" fill="none" stroke="#eb3d1f" stroke-width="1.5"/></svg>
    <div class="footer__brand"><span class="dot"></span>RIVO</div>
    <div class="footer__nav"><span>HOME</span><span>ABOUT</span><span>SERVICES</span><span>GALLERY</span><span>CONTACT</span></div>
    <div class="footer__badges"><span></span><span></span><span></span><span></span><span></span></div>
  </footer>
</main>

<main class="page page--b">
  <nav class="section nav">
    <span>HOME</span><span>ABOUT</span>
    <span class="nav__brand"><span class="dot"></span>RIVO</span>
    <span>SERVICES</span><span>GALLERY</span><span class="nav__cta">BOOK NOW</span>
  </nav>
  <header class="section hero">
    <div class="hero__photo" role="img" aria-label="Engine bay of a car under repair"></div>
    <div class="hero__copy">
      <h1 class="hero__title">Specializing in Navoro and Omvar <em>auto repair</em></h1>
      <p class="hero__sub">Fixed right the first time, every visit.</p>
      <span class="btn">SCHEDULE APPOINTMENT</span>
    </div>
    <svg class="hero__edge" viewBox="0 0 338 30" preserveAspectRatio="none"><polygon points="0,8 169,26 338,8 338,30 0,30" fill="#0a0a0a"/><polyline points="0,8 169,26 338,8" fill="none" stroke="#eb3d1f" stroke-width="2"/></svg>
  </header>
  <section class="section about">
    <div class="about__mark"><span class="dot"></span>RIVO</div>
    <div class="about__text">
      <h2 class="h2">ABOUT RIVO</h2>
      <p>For seven years our certified technicians have cared for Navoro and Omvar owners, plus other Asian imports. We use quality parts, honest pricing and careful work so every repair is done right the first time.</p>
      <span class="btn btn--ghost">LEARN MORE</span>
    </div>
  </section>
  <section class="section services">
    <h2 class="h2 center">SERVICES PROVIDE</h2>
    <div class="services__grid">
      <div>
        <div class="svc svc--active"><i class="svc__icon"></i>Oil Change</div>
        <div class="svc"><i class="svc__icon"></i>Brake Repair</div>
        <div class="svc"><i class="svc__icon"></i>Engine Diagnostics</div>
        <div class="svc"><i class="svc__icon"></i>Tune Up</div>
        <div class="svc"><i class="svc__icon"></i>Timing Belt</div>
        <div class="svc"><i class="svc__icon"></i>Battery Service</div>
      </div>
      <div>
        <div class="svc"><i class="svc__icon"></i>Transmission Service</div>
        <div class="svc"><i class="svc__icon"></i>Suspension Repair</div>
        <div class="svc"><i class="svc__icon"></i>Steering Repair</div>
        <div class="svc"><i class="svc__icon"></i>Cooling System</div>
        <div class="svc"><i class="svc__icon"></i>Exhaust Repair</div>
        <div class="svc"><i class="svc__icon"></i>Wheel Alignment</div>
      </div>
      <div>
        <div class="svc"><i class="svc__icon"></i>AC Repair</div>
        <div class="svc"><i class="svc__icon"></i>Electrical Repair</div>
        <div class="svc"><i class="svc__icon"></i>Check Engine Light</div>
        <div class="svc"><i class="svc__icon"></i>Fuel System</div>
        <div class="svc"><i class="svc__icon"></i>Hybrid Service</div>
        <div class="svc"><i class="svc__icon"></i>Inspections</div>
      </div>
    </div>
  </section>
  <section class="section gallery">
    <svg class="gallery__edge" viewBox="0 0 338 24" preserveAspectRatio="none"><polygon points="0,0 338,0 338,4 169,22 0,4" fill="#151515"/></svg>
    <h2 class="h2 center">OUR GALLERY</h2>
    <div class="gallery__grid">
      <div class="shot" role="img" aria-label="Shop photo of engine work"></div>
      <div class="shot" role="img" aria-label="Shop photo of a sedan on the lift"></div>
      <div class="shot" role="img" aria-label="Shop photo of engine parts"></div>
      <div class="shot" role="img" aria-label="Shop photo of a technician's bench"></div>
      <div class="shot" role="img" aria-label="Shop photo of an SUV in the bay"></div>
      <div class="shot" role="img" aria-label="Shop photo of a car in the lot"></div>
      <div class="shot" role="img" aria-label="Shop photo of cars outside the shop"></div>
      <div class="shot" role="img" aria-label="Shop photo of a repaired vehicle"></div>
    </div>
  </section>
  <section class="section brands">
    <p class="brands__text">RIVO AUTOMOTIVE SPECIALIZES IN NAVORO &amp; OMVAR<br>AUTO REPAIR BUT ALSO SERVICE AND REPAIR<br>OTHER ASIAN IMPORT VEHICLES</p>
    <div class="brands__row">
      <span class="badge"></span><span class="badge badge--sq"></span><span class="badge"></span><span class="badge badge--sq"></span>
      <span class="badge badge--sq"></span><span class="badge"></span><span class="badge badge--sq"></span><span class="badge"></span>
    </div>
    <span class="btn">SCHEDULE APPOINTMENT</span>
  </section>
  <section class="section contact">
    <div class="contact__info">
      <h2 class="contact__title">CONTACT <em>US</em></h2>
      <p>Questions about your vehicle? Call or send a message and we will reply soon.</p>
      <div class="contact__line"><span class="dot"></span>(555) 018-2247</div>
      <div class="contact__line"><span class="dot"></span>hello@rivoauto.example</div>
      <div class="contact__line"><span class="dot"></span>120 Harbor Lane, Springvale</div>
    </div>
    <form class="contact__form">
      <div class="form__label">LEAVE US A MESSAGE</div>
      <div class="field">Name</div>
      <div class="field">Email</div>
      <div class="field">Phone</div>
      <div class="field field--area">Message</div>
      <span class="btn">SEND</span>
    </form>
  </section>
  <footer class="section footer">
    <svg class="footer__edge" viewBox="0 0 338 14" preserveAspectRatio="none"><polyline points="0,12 169,2 338,12" fill="none" stroke="#eb3d1f" stroke-width="1.5"/></svg>
    <div class="footer__brand"><span class="dot"></span>RIVO</div>
    <div class="footer__nav"><span>HOME</span><span>ABOUT</span><span>SERVICES</span><span>GALLERY</span><span>CONTACT</span></div>
    <div class="footer__badges"><span></span><span></span><span></span><span></span><span></span></div>
  </footer>
</main>

</body>
</html>
```